Business Card for Polygraph business in Africa

Business Card . Polygraph Examiner based in Tanzania, East Africa.
Business Card will be used to disseminate contact information to potential clients.
It should convey that I am a professional specifically in the polygraph field and perform my work with integrity.

I have attached the business card that I'm currently using, which I threw together myself initially. It's not professional enough.

Target Market(s)

Banks, Accounting Firms, Government Ministries, Gas, Oil, & Gemstone Mining Concerns, Wildlife Conservation NGOs, International companies located in East Africa.

Industry/Entity Type

Business

Contact Information for Business Card

Veritrace Kilonga
Miriam Holloway
PO Box 48317
Arusha, Tanzania
+255 612 839 274
miriamholloway@postvale.example

Colors
00a990
f37122
faa54b

Requirements
Must have
• - Veritrace Kilonga (with the word "Polygraph" being more prominent than the word "Tanzania")
• - Forensic Examinations
• - Employment Screening
• - Should contain a logo of the Continental Truthline Society (of which I'm a member)
• - I would like an accent design (such as the polygraph "squiggles" of a cardio tracing or such as that)
• - My contact information (less prominent, but large enough to read legibly). I would also consider putting the contact information on the second side of the card.
Nice to have
• My color suggestions are changeable.
Should not have
• Anything "cutesy" or "cartoonish"

```html
<!DOCTYPE html>
<html lang="en">
<head>
<meta charset="utf-8">
<title>Veritrace Kilonga — Business Card</title>
<link rel="stylesheet" href="https://fonts.googleapis.com/css2?family=Work+Sans:wght@400;500;700&display=swap">
<style>
  :root {
    --orange: #f37122;
    --orange-light: #f7893f;
    --orange-deep: #ee6a1d;
    --navy: #1f2b6e;
    --ink: #141414;
    --white: #ffffff;
    --backdrop: #2b2b2b;
  }
  * { box-sizing: border-box; margin: 0; padding: 0; }
  html, body {
    width: 1200px; height: 930px; overflow: hidden;
    background: var(--backdrop);
    font-family: "Work Sans", Arial, sans-serif;
  }
  .stage { position: relative; width: 1200px; height: 930px; }
  .card {
    position: absolute; width: 560px; height: 320px;
    border-radius: 22px; overflow: hidden;
    box-shadow: 0 14px 30px rgba(0,0,0,.45);
  }
  .card-front {
    left: 80px; top: 100px;
    background: linear-gradient(100deg, var(--orange-deep) 0%, var(--orange) 35%, var(--orange-light) 50%, var(--orange) 65%, var(--orange-deep) 100%);
  }
  .front-brand {
    position: absolute; left: 170px; top: 140px;
    color: var(--white); font-weight: 700; font-size: 30px; letter-spacing: .2px;
  }
  .card-back { left: 560px; top: 510px; background: var(--white); }
  .back-top { position: absolute; left: 0; top: 0; width: 100%; height: 178px; background: var(--white); }
  .back-brand {
    position: absolute; left: 64px; top: 98px;
    color: var(--ink); font-weight: 700; font-size: 25px;
  }
  .member-seal {
    position: absolute; right: 40px; top: 22px; width: 118px; height: 118px;
  }
  .divider { position: absolute; left: 0; top: 178px; width: 100%; height: 3px; background: var(--ink); }
  .back-bottom {
    position: absolute; left: 0; top: 181px; width: 100%; height: 139px;
    background: linear-gradient(100deg, var(--orange-deep) 0%, var(--orange) 40%, var(--orange-light) 55%, var(--orange) 75%, var(--orange-deep) 100%);
    color: var(--white);
  }
  .holder-name {
    position: absolute; left: 40px; top: 16px;
    font-size: 24px; font-weight: 500; letter-spacing: 1px; text-transform: uppercase;
  }
  .contact { position: absolute; left: 40px; top: 52px; font-size: 13px; line-height: 17px; }
  .contact-line { display: flex; align-items: center; gap: 8px; }
  .contact-line svg { width: 11px; height: 11px; flex: none; }
  .services {
    position: absolute; right: 34px; top: 30px; text-align: right;
    font-size: 13px; line-height: 20px; letter-spacing: .6px; text-transform: uppercase;
  }
</style>
</head>
<body>
<main class="stage">
  <section class="card card-front" aria-label="Card front">
    <div class="front-brand">Veritrace Kilonga</div>
  </section>

  <section class="card card-back" aria-label="Card back">
    <div class="back-top">
      <div class="back-brand">Veritrace Kilonga</div>
      <svg class="member-seal" viewBox="0 0 118 118" role="img" aria-label="Continental Truthline Society membership seal">
        <circle cx="59" cy="59" r="56" fill="none" stroke="var(--navy)" stroke-width="6"/>
        <circle cx="59" cy="59" r="42" fill="none" stroke="var(--navy)" stroke-width="2"/>
      </svg>
    </div>
    <div class="divider"></div>
    <div class="back-bottom">
      <div class="holder-name">Miriam Holloway</div>
      <div class="contact">
        <div class="contact-line">PO Box 48317</div>
        <div class="contact-line">Arusha, Tanzania</div>
        <div class="contact-line">
          <svg viewBox="0 0 24 24" aria-hidden="true"><path fill="var(--white)" d="M6.6 10.8a15 15 0 0 0 6.6 6.6l2.2-2.2a1 1 0 0 1 1-.25 11.4 11.4 0 0 0 3.6.57 1 1 0 0 1 1 1V20a1 1 0 0 1-1 1A17 17 0 0 1 3 4a1 1 0 0 1 1-1h3.5a1 1 0 0 1 1 1c0 1.25.2 2.45.57 3.57a1 1 0 0 1-.25 1z"/></svg>
          +255 612 839 274
        </div>
        <div class="contact-line">
          <svg viewBox="0 0 24 24" aria-hidden="true"><rect x="2" y="5" width="20" height="14" rx="1.5" fill="none" stroke="var(--white)" stroke-width="2"/><path d="M2.5 6l9.5 7 9.5-7" fill="none" stroke="var(--white)" stroke-width="2"/></svg>
          miriamholloway@postvale.example
        </div>
      </div>
      <div class="services">
        <div>Issue Investigation</div>
        <div>Employment Screening</div>
      </div>
    </div>
  </section>
</main>
</body>
</html>
```